wardrobe/costume stylist needs good business card for own business

Hi:)

I'm wanting a business card for my company. I am a freelance stylist.

I do wardrobe/costume stylist to TV commercials; Films; Fashion and Lifestyle shoots.

I'd like a design based around my name Rosalind Parfrey written nicely, maybe a colour? Up to you?!

I've attached a couple of images of business cards I like
.... be creative and have fun!

Thank you :)

Reason: I was trying to get my new business card ready for before I headed overseas Friday morning but I don't think that was realistic so I'd like to extend the deadline to give time to the project. Thank you

Hi designers:) Thank you for all your designs, I've extended the deadline until Sunday, so there's a bit more time. I've attached 3 pictures of business cards which I quite like, please take a look to see if it can be of help in your process. I like the pale plain or patterned background with dark font and the dark plain or patterned background with the pale font the motifs the feminine fonts the plain fonts I like the idea of playing with a circle or some shape on one side of the card with my name or initials as in the picture I have on my post could you play around with this idea a bit please? Thank you all for the work you've done :) Rosa

Hi I am working overseas til Saturday night sorry for no feedback until I teturn Thanks :) Rosa

Hi designers, Thank you all so much for submitting your designs, I really appreciate your input into my project :) I'm sorry I didn't get to respond to some comments, and give feedback. I didn't back from being away until later than I expected, and the deadline had passed then, so apologies. Thanks to you all again for all your really good designs :) Rosa

Target Market(s)

I am a freelance stylist my target audience is producers, production companies, photographers, directors...

Industry/Entity Type

Business

Requirements
Must have
• Rosalind Parfrey
Stylist or Wardrobe Stylist

email rosaparfrey@mailbox-example.co.nz
Mobile 0218467193

(Don't have to use the words 'email' and 'mobile')
Nice to have
• Would like it to be double sided
Like B & W
Like pale colour background with dark font or white font
Like dark colour background with pale font
Should not have
• I would prefer it not to incorporate pictures

```html
<!DOCTYPE html>
<html lang="en">
<head>
<meta charset="utf-8">
<title>Rosalind Parfrey – Stylist Business Card</title>
<link href="https://fonts.googleapis.com/css2?family=Pinyon+Script&family=Open+Sans:wght@400&family=PT+Sans+Narrow&display=swap" rel="stylesheet">
<style>
  :root {
    --backdrop: #e2e2e2;
    --card: #ead5b6;
    --ink: #5e5c5a;
    --ink-soft: #6d6a66;
    --paper-white: #ffffff;
    --ring-tone: #c9b79f;
    --mark-dark: #58585a;
  }
  html, body {
    margin: 0;
    width: 1200px;
    height: 1000px;
    overflow: hidden;
    background: radial-gradient(ellipse at 50% 45%, #f0f0f0 0%, var(--backdrop) 70%, #d2d2d2 100%);
  }
  .canvas {
    position: relative;
    width: 1200px;
    height: 1000px;
  }
  .card {
    position: absolute;
    width: 560px;
    height: 320px;
    background: var(--card);
    box-shadow: 0 6px 18px rgba(0, 0, 0, 0.18);
  }
  .card--back { left: 480px; top: 170px; }
  .card--front { left: 260px; top: 520px; }

  /* Back side: name mark */
  .brand-mark {
    position: absolute;
    right: 44px;
    top: 50%;
    transform: translateY(-50%);
    display: flex;
    align-items: center;
    gap: 16px;
  }
  .brand-mark__dot {
    width: 22px;
    height: 22px;
    border-radius: 50%;
    background: var(--mark-dark);
  }
  .brand-mark__name {
    font-family: "Open Sans", sans-serif;
    font-weight: 400;
    font-size: 26px;
    color: var(--mark-dark);
    letter-spacing: 0.5px;
  }

  /* Front side */
  .person-name {
    position: absolute;
    left: 0;
    right: 0;
    top: 34px;
    margin: 0;
    text-align: center;
    font-family: "Pinyon Script", cursive;
    font-weight: 400;
    font-size: 54px;
    line-height: 1.1;
    white-space: nowrap;
  }
  .person-name__first { color: var(--ink); }
  .person-name__last { color: var(--paper-white); }

  .role-badge {
    position: absolute;
    left: 118px;
    top: 128px;
    width: 150px;
    height: 150px;
  }
  .role-badge svg { position: absolute; inset: 0; }
  .role-badge__label {
    position: absolute;
    inset: 0;
    display: flex;
    align-items: center;
    justify-content: center;
    font-family: "Open Sans", sans-serif;
    font-size: 22px;
    color: var(--ink);
  }

  .contact {
    position: absolute;
    right: 28px;
    top: 226px;
    margin: 0;
    text-align: center;
    font-family: "PT Sans Narrow", sans-serif;
    font-style: normal;
    font-size: 17px;
    line-height: 1.35;
    color: var(--ink-soft);
    white-space: nowrap;
  }
</style>
</head>
<body>
<main class="canvas">

  <section class="card card--back" aria-label="Business card, back">
    <div class="brand-mark">
      <span class="brand-mark__dot"></span>
      <span class="brand-mark__name">Rosalind Parfrey</span>
    </div>
  </section>

  <section class="card card--front" aria-label="Business card, front">
    <h1 class="person-name">
      <span class="person-name__first">Rosalind</span>
      <span class="person-name__last">Parfrey</span>
    </h1>

    <div class="role-badge">
      <svg viewBox="0 0 150 150" role="img" aria-label="Decorative ring of dots around the job title">
        <defs>
          <radialGradient id="ringTone" cx="50%" cy="50%" r="50%">
            <stop offset="55%" stop-color="#ead5b6" stop-opacity="0"/>
            <stop offset="78%" stop-color="#c9b79f" stop-opacity="0.55"/>
            <stop offset="100%" stop-color="#ead5b6" stop-opacity="0"/>
          </radialGradient>
        </defs>
        <circle cx="75" cy="75" r="75" fill="url(#ringTone)"/>
      </svg>
      <span class="role-badge__label">Stylist</span>
    </div>

    <address class="contact">
      <div class="contact__email">rosaparfrey@mailbox-example.co.nz</div>
      <div class="contact__phone">0218467193</div>
    </address>
  </section>

</main>
</body>
</html>
```